Copperleaf Balustrade Website Redesign

I want a fresh new design for my website. Original website
www.copperleafbalustrade-example.com. Will need to add additional photos for winning designer. Please use the basic layout for new design. Looking to get a more modern, functional site to attract new customer and ne bale to highlight past projects. Need it to be easy to navigate and get in touch with me for inquiries.

Target Market(s)

Builders and home owners in WA state

Industry/Entity Type

Building, Construction, Deck building

Coding

Coded - Design and coding required

Number of Pages Required

5+ page

Font styles to use
Sans Serif

Colors
0054AA
0677BA
7BADD7
CADEEF
E8F1F8
0094D4
00A9DD
6FCCEA
C7EBF8
E9F6FB
00AB8E
00BBA5
67D7C9
C6EFE9
E9F9F6
59FF00
82FF00
B8FF75
E3FFCB
F4FFEA

Requirements
Must have
• Will need to add more photos of completed projects
Nice to have
• Fresh take on old website, something modern
Should not have
• Nothing comes to mind

```html
<!DOCTYPE html>
<html lang="en">
<head>
<meta charset="utf-8">
<title>Copperleaf Balustrade</title>
<link href="https://fonts.googleapis.com/css2?family=Roboto:wght@400;500;700&family=Montserrat:wght@700&display=swap" rel="stylesheet">
<style>
:root{
  --navy:#1f3f94;
  --deep:#0f1d3d;
  --green:#2a9a72;
  --green-btn:#1e8a64;
  --tile:#1e6fb8;
  --tile-dark:#17568f;
  --grey:#f0f0f0;
  --ink:#1d1d1d;
  --body:#3a3a3a;
  --white:#fff;
}
*{box-sizing:border-box;margin:0;padding:0}
html,body{width:1200px;height:4515px;overflow:hidden;background:var(--white)}
body{position:relative;font-family:'Roboto',sans-serif;color:var(--ink)}
.abs{position:absolute}
.photo{position:absolute}

/* nav */
.nav{left:0;top:0;width:1200px;height:79px;background:var(--navy)}
.nav a{position:absolute;top:0;height:79px;line-height:79px;color:#fff;font-size:14px;text-decoration:none;transform:translateX(-50%)}
.nav .active{background:var(--green);width:75px;text-align:center}
.brand{left:526px;top:0;width:150px;height:161px;background:#fff;clip-path:polygon(0 0,100% 0,100% 86%,50% 100%,0 86%);text-align:center;padding-top:52px;color:var(--green);font-weight:700;font-size:15px;line-height:22px;letter-spacing:.5px}

/* hero */
.hero{left:0;top:79px;width:1200px;height:600px;background:linear-gradient(180deg,#3e4244 0%,#5b5f5d 45%,#2f3330 100%)}
.hero-title{left:0;width:1200px;top:340px;text-align:center;color:#fff;font-family:'Montserrat',sans-serif;font-size:58px;font-weight:700}
.hero-sub{left:0;width:1200px;top:418px;text-align:center;color:#fff;font-size:28px}
.btn{position:absolute;background:var(--green-btn);color:#fff;font-weight:700;text-align:center}
.hero-btn{left:527px;top:475px;width:146px;height:45px;line-height:45px;font-size:13px}
.circ{position:absolute;border-radius:50%;display:flex;align-items:center;justify-content:center}
.hero-arrow{width:48px;height:48px;background:rgba(0,0,0,.35);border:1px solid rgba(255,255,255,.4);top:353px}
.band{left:0;top:590px;width:1200px;height:100px}

/* products */
.prod-label{top:924px;width:278px;text-align:center;font-size:16px;font-weight:500}
.prod-label span{display:block;width:100px;height:2px;background:var(--green);margin:6px auto 0}

/* about */
.about-photo{left:144px;top:1049px;width:439px;height:398px;background:linear-gradient(160deg,#8d9290,#4f5553 60%,#3a3f3d)}
.about-square{left:137px;top:1042px;width:115px;height:123px;background:var(--navy);border:7px solid #fff;box-sizing:border-box;border-width:0 14px 14px 0}
.about-h{left:617px;top:1043px;font-size:23px;font-weight:700}
.about-lic{left:617px;top:1076px;font-size:23px;font-weight:700;color:var(--green)}
.about-text{left:617px;top:1130px;width:440px;font-size:13px;line-height:22px;color:var(--body);text-align:justify}
.about-text p{margin-bottom:14px}

/* why */
.why{left:0;top:1538px;width:1200px;height:557px;background:var(--grey)}
.sec-title{position:absolute;left:0;width:1200px;text-align:center;font-size:34px;font-weight:700}
.rule{position:absolute;left:540px;width:120px;height:2px;background:var(--green)}
.tile{position:absolute;width:144px;height:144px;background:linear-gradient(135deg,var(--tile) 50%,var(--tile-dark) 50%);display:flex;align-items:center;justify-content:center}
.feat{position:absolute;width:283px}
.feat h3{font-size:19px;line-height:28px;font-weight:500}
.feat p{font-size:13px;line-height:22px;color:var(--body);margin-top:10px}
.feat.l{text-align:right}
.feat.r{text-align:justify}
.feat.r h3{text-align:left}

/* process */
.process{left:0;top:2095px;width:1200px;height:656px;background:var(--green)}
.proc-circle{width:158px;height:158px;background:#fff;top:2274px}
.proc-h{position:absolute;top:2440px;width:240px;text-align:center;color:#fff;font-size:17px;font-weight:500}
.proc-p{position:absolute;top:2472px;width:180px;text-align:center;color:#fff;font-size:13px;line-height:20px}

/* serving */
.serve-h{left:144px;top:2816px;font-size:36px;line-height:44px;font-weight:700}
.serve-p{left:144px;top:2933px;width:439px;font-size:13px;line-height:22px;color:var(--body);text-align:justify}
.serve-photo{left:629px;top:2819px;width:427px;height:238px;background:linear-gradient(180deg,#7aa0c4 0%,#d8a876 55%,#5a4a42 100%)}
.serve-frame{left:948px;top:2959px;width:129px;height:118px;border:2px solid var(--navy);border-left:none;border-top:none}

/* projects */
.proj-photo{position:absolute;top:3245px;width:281px;height:343px}
.proj-label{position:absolute;top:3551px;width:235px;height:41px;line-height:46px;background:#fff;text-align:center;font-size:19px;font-weight:500}
.proj-text{position:absolute;top:3600px;width:281px;text-align:center;font-size:13px;line-height:20px;color:var(--body)}
.proj-arrow{width:48px;height:48px;background:var(--green-btn);top:3424px}

/* contact + footer */
.footer{left:0;top:3937px;width:1200px;height:578px;background:var(--deep)}
.banner{left:144px;top:3756px;width:912px;height:277px;background:var(--green);text-align:center;color:#fff}
.banner h2{font-size:34px;font-weight:700;margin-top:64px}
.banner p{font-size:13px;line-height:22px;width:620px;margin:26px auto 0}
.f-h{position:absolute;color:#fff;font-size:19px;font-weight:700}
.f-links{left:131px;top:4118px;color:#fff;font-size:15px;line-height:24px;list-style:none}
.f-icon{width:44px;height:44px;background:var(--green)}
.f-txt{position:absolute;left:447px;color:#fff;font-size:13px;line-height:22px}
.f-txt b{font-weight:500}
.field{position:absolute;border:1px solid #fff;color:#fff;font-size:13px;padding:12px 14px}
.submit{left:694px;top:4368px;width:196px;height:38px;line-height:38px;font-size:13px}
.social{width:42px;height:42px;top:4362px}
.copy{left:35px;top:4445px;width:1128px;height:70px;background:var(--navy);color:#fff;font-size:13px;text-align:center;line-height:70px}
</style>
</head>
<body>

<!-- hero -->
<div class="abs hero photo" role="img" aria-label="Modern dark-sided home with glass deck railings and exterior stairway"></div>
<div class="abs hero-title">Copperleaf Balustrade</div>
<div class="abs hero-sub">Durable, stylish, and built for the Pacific Northwest.</div>
<div class="btn hero-btn">GET STARTED</div>
<div class="circ hero-arrow" style="left:46px"><svg width="12" height="12" viewBox="0 0 12 12"><path d="M8 2 4 6l4 4" stroke="#fff" stroke-width="1.5" fill="none"/></svg></div>
<div class="circ hero-arrow" style="left:1103px"><svg width="12" height="12" viewBox="0 0 12 12"><path d="M4 2l4 4-4 4" stroke="#fff" stroke-width="1.5" fill="none"/></svg></div>

<svg class="abs band" viewBox="0 0 1200 100" preserveAspectRatio="none"><polygon points="0,85 600,6 1200,85 1200,100 0,100" fill="#fff"/></svg>
<div class="abs" style="left:0;top:689px;width:1200px;height:300px;background:#fff"></div>

<!-- nav -->
<nav class="abs nav">
  <a class="active" style="left:163px">HOME</a>
  <a style="left:266px">PRODUCTS</a>
  <a style="left:371px">ABOUT</a>
  <a style="left:792px">SERVICES</a>
  <a style="left:906px">PROJECTS</a>
  <a style="left:1020px">CONTACT</a>
</nav>
<div class="abs brand">COPPERLEAF<br>BALUSTRADE</div>

<!-- products -->
<div class="photo" style="left:16px;top:652px;width:278px;height:263px;background:linear-gradient(135deg,#8fa38a,#4d5a50)" role="img" aria-label="Aluminum railing along a wooden boardwalk"></div>
<div class="photo" style="left:312px;top:645px;width:278px;height:270px;background:linear-gradient(180deg,#3f78c9,#9cc6ea 55%,#4f7fa8)" role="img" aria-label="Glass railing overlooking water under a blue sky"></div>
<div class="photo" style="left:610px;top:645px;width:277px;height:270px;background:linear-gradient(180deg,#cfd3d2,#8a8d86 60%,#5e5f5a)" role="img" aria-label="Cable railing bridge through forest"></div>
<div class="photo" style="left:906px;top:652px;width:277px;height:263px;background:linear-gradient(135deg,#a89c8c,#4a3f36)" role="img" aria-label="Custom interior staircase railing"></div>
<div class="abs prod-label" style="left:16px">Aluminum Railings<span></span></div>
<div class="abs prod-label" style="left:312px;color:var(--green)">Glass Railings<span></span></div>
<div class="abs prod-label" style="left:610px">Cable Railings<span></span></div>
<div class="abs prod-label" style="left:906px">Custom<span></span></div>

<!-- about -->
<div class="photo about-photo" role="img" aria-label="Home balcony with glass panel railing"></div>
<div class="abs about-square"></div>
<div class="abs about-h">LICENSED, INSURED, &amp; BONDED</div>
<div class="abs about-lic">WA GC LICENSE # COPPEBL914KQ</div>
<div class="abs about-text">
  <p>Formed in 2020</p>
  <p>At Copperleaf Balustrade, we believe that every outdoor space deserves the perfect blend of style, safety, and durability. Serving homeowners, builders, and commercial developers across the Washington State, we specialize in crafting custom railing systems designed to withstand the region's unique climate while enhancing the beauty of your outdoor living spaces.</p>
  <p>With a focus on premium materials, expert craftsmanship, and exceptional customer service, Copperleaf Balustrade is proud to be the trusted partner for both residential and commercial railing projects. Whether you're looking to complement a new deck, add a modern touch to your balcony, or create a secure and stunning barrier for a commercial space, we've got the perfect solution for you.</p>
</div>

<!-- why -->
<div class="abs why"></div>
<div class="sec-title" style="top:1608px">WHY CHOOSE COPPERLEAF BALUSTRADE ?</div>
<div class="rule" style="top:1664px;left:520px;width:160px"></div>

<div class="feat l" style="left:139px;top:1694px"><h3>LOCALLY CRAFTED,<br>REGIONALLY RESILIENT</h3><p>Our railings are designed with the Pacific Northwest's weather in mind—rain, snow, and everything in between.</p></div>
<div class="feat l" style="left:139px;top:1862px"><h3>CUSTOM SOLUTIONS<br>FOR EVERY NEED</h3><p>We work closely with you to design and fabricate custom railing systems that perfectly suit your space,</p></div>
<div class="feat r" style="left:776px;top:1694px"><h3>EXPERT INSTALLATION<br>&amp; CRAFTSMANSHIP</h3><p>Our skilled craftsmen take pride in delivering exceptional workmanship, while our professional installers</p></div>
<div class="feat r" style="left:776px;top:1862px"><h3>FULL-SERVICE<br>PARTNER</h3><p>From the initial consultation and design process to installation and ongoing maintenance, we are with</p></div>

<div class="tile" style="left:445px;top:1694px"><svg width="64" height="80" viewBox="0 0 64 80" fill="none" stroke="#fff" stroke-width="5"><path d="M14 4v72M50 4v72M14 16h36M14 30h36M14 44h36M14 58h36"/></svg></div>
<div class="tile" style="left:608px;top:1694px"><svg width="80" height="70" viewBox="0 0 80 70" fill="#fff"><polygon points="40,4 76,22 40,40 4,22"/><path d="M4 34l36 18 36-18v8L40 60 4 42z"/><path d="M4 48l36 18 36-18v4L40 70 4 52z" opacity=".9"/></svg></div>
<div class="tile" style="left:445px;top:1862px"><svg width="76" height="76" viewBox="0 0 76 76" stroke="#fff" stroke-width="7" stroke-linecap="round"><path d="M12 12l52 52M64 12L20 56"/><circle cx="16" cy="60" r="6" fill="#fff"/></svg></div>
<div class="tile" style="left:608px;top:1862px"><svg width="84" height="84" viewBox="0 0 84 84"><circle cx="42" cy="42" r="28" fill="none" stroke="#fff" stroke-width="12" stroke-dasharray="11 6"/><circle cx="42" cy="42" r="22" fill="none" stroke="#fff" stroke-width="8"/></svg></div>

<!-- process -->
<div class="abs process photo" role="img" aria-label="Green-tinted backdrop of a deck railing"></div>
<svg class="abs" style="left:0;top:2670px" width="1200" height="82" viewBox="0 0 1200 82"><polygon points="0,82 600,5 1200,82" fill="#fff"/></svg>
<div class="sec-title" style="top:2170px;color:#fff">OUR PROCESS</div>
<div class="rule" style="top:2222px;background:#fff"></div>

<div class="circ proc-circle" style="left:217px"><svg width="70" height="70" viewBox="0 0 70 70" fill="none" stroke="var(--green)" stroke-width="3"><circle cx="20" cy="18" r="7"/><circle cx="50" cy="18" r="7"/><path d="M8 60V34h24v26M38 60V34h24v26M30 8h12v10H30"/></svg></div>
<div class="circ proc-circle" style="left:520px"><svg width="70" height="70" viewBox="0 0 70 70" fill="none" stroke="var(--green)" stroke-width="3"><circle cx="33" cy="33" r="22" stroke-dasharray="8 4"/><circle cx="33" cy="33" r="10"/><circle cx="50" cy="50" r="11" fill="#fff"/><path d="M45 50l4 4 7-8"/></svg></div>
<div class="circ proc-circle" style="left:827px"><svg width="70" height="70" viewBox="0 0 70 70" fill="none" stroke="var(--green)" stroke-width="3"><circle cx="22" cy="16" r="6"/><circle cx="35" cy="12" r="6"/><circle cx="48" cy="16" r="6"/><path d="M14 34h42v8H14zM4 40l12 20h38l12-20"/></svg></div>

<svg class="abs" style="left:407px;top:2338px" width="82" height="30" viewBox="0 0 82 30" fill="none" stroke="#fff" stroke-width="3"><path d="M2 20C25 6 55 6 76 18"/><path d="M66 12l10 6-8 8"/></svg>
<svg class="abs" style="left:713px;top:2338px" width="82" height="30" viewBox="0 0 82 30" fill="none" stroke="#fff" stroke-width="3"><path d="M2 20C25 6 55 6 76 18"/><path d="M66 12l10 6-8 8"/></svg>

<div class="proc-h" style="left:176px">Consultation &amp; Design</div>
<div class="proc-h" style="left:479px">Professional Installation</div>
<div class="proc-h" style="left:786px">Ongoing Support</div>
<div class="proc-p" style="left:206px">We start by listening to your vision and understanding your specific needs. Our team will offer expert advice and design ideas to help you choose the best materials and styles.</div>
<div class="proc-p" style="left:509px">Our experienced team handles all aspects of installation, from measuring to securing, ensuring your railing is safe, secure, and perfectly aligned.</div>
<div class="proc-p" style="left:816px">We offer warranties on all of our products and services, and we are always available to help with maintenance or modifications down the road.</div>

<!-- serving -->
<div class="abs serve-h">SERVING WASHINGTON<br>STATE</div>
<div class="abs" style="left:144px;top:2914px;width:200px;height:2px;background:var(--green)"></div>
<div class="abs serve-p">Copperleaf Balustrade is proud to serve the entire state of Washington. Whether you're upgrading your home's deck or outfitting a commercial space, we understand the importance of creating beautiful, durable railings that stand up to the region's diverse and often challenging weather conditions.</div>
<div class="abs serve-frame"></div>
<div class="photo serve-photo" role="img" aria-label="City skyline with observation tower at sunset"></div>

<!-- projects -->
<div class="sec-title" style="top:3156px">PAST PROJECTS</div>
<div class="rule" style="top:3213px;left:530px;width:140px"></div>
<div class="circ proj-arrow" style="left:48px"><svg width="12" height="12" viewBox="0 0 12 12"><path d="M8 2 4 6l4 4" stroke="#fff" stroke-width="1.5" fill="none"/></svg></div>
<div class="circ proj-arrow" style="left:1103px"><svg width="12" height="12" viewBox="0 0 12 12"><path d="M4 2l4 4-4 4" stroke="#fff" stroke-width="1.5" fill="none"/></svg></div>

<div class="proj-photo" style="left:144px;background:linear-gradient(160deg,#d9d6cc,#8f8a7e)" role="img" aria-label="Apartment balconies with black metal railings"></div>
<div class="proj-photo" style="left:459px;background:linear-gradient(180deg,#b8c6d2,#6d7a5a 50%,#7c7f80)" role="img" aria-label="Deck railing overlooking a town and hills"></div>
<div class="proj-photo" style="left:774px;background:linear-gradient(160deg,#b7b7b4,#6a6a66)" role="img" aria-label="Exterior staircase with black metal railing"></div>
<div class="proj-label" style="left:166px">LOREM IPSUM DOL</div>
<div class="proj-label" style="left:481px">LOREM IPSUM DOL</div>
<div class="proj-label" style="left:796px">LOREM IPSUM DOL</div>
<div class="proj-text" style="left:144px">Lorem ipsum dolor sit amet, consec tetur adipiscing elit, sed do eiusmod tempor incididunt</div>
<div class="proj-text" style="left:459px">Lorem ipsum dolor sit amet, consec tetur adipiscing elit, sed do eiusmod tempor incididunt</div>
<div class="proj-text" style="left:774px">Lorem ipsum dolor sit amet, consec tetur adipiscing elit, sed do eiusmod tempor incididunt</div>

<!-- footer -->
<div class="abs footer photo" role="img" aria-label="Dark navy tinted city backdrop"></div>
<svg class="abs" style="left:0;top:3925px" width="1200" height="40" viewBox="0 0 1200 40"><path d="M0 0H1200V40C900 10 300 10 0 40Z" fill="#fff"/></svg>

<div class="abs banner">
  <h2>CONTACT US TODAY</h2>
  <p>Ready to elevate your space with a custom railing solution that's built to last? Reach out to the Copperleaf Balustrade team for a free consultation. Let us bring your vision to life with craftsmanship, care, and precision.</p>
</div>

<div class="f-h" style="left:131px;top:4072px">QUICK LINKS</div>
<ul class="abs f-links"><li>Home</li><li>About Us</li><li>Services</li><li>Projects</li><li>Blog</li><li>Reviews</li><li>Contact Us</li></ul>

<div class="f-h" style="left:387px;top:4072px">CONTACT US</div>
<div class="circ f-icon" style="left:388px;top:4123px"><svg width="18" height="22" viewBox="0 0 18 22"><path d="M9 1a7 7 0 0 0-7 7c0 5 7 13 7 13s7-8 7-13a7 7 0 0 0-7-7z" fill="#fff"/><circle cx="9" cy="8" r="3" fill="var(--green)"/></svg></div>
<div class="circ f-icon" style="left:388px;top:4202px"><svg width="22" height="16" viewBox="0 0 22 16"><rect width="22" height="16" rx="2" fill="#fff"/><path d="M1 2l10 7 10-7" stroke="var(--green)" stroke-width="1.6" fill="none"/></svg></div>
<div class="circ f-icon" style="left:388px;top:4263px"><svg width="20" height="20" viewBox="0 0 20 20"><path d="M4 1l4 4-2 3c1 3 3 5 6 6l3-2 4 4-3 3C8 19 1 12 1 4z" fill="#fff"/></svg></div>
<div class="f-txt" style="top:4123px">4218 Cedarline Ave<br>Yakima, WA 98901</div>
<div class="f-txt" style="top:4181px"><b>Email Address :</b><br>info@copperleafbalustrade-example.com</div>
<div class="f-txt" style="top:4250px"><b>Phone :</b><br>(206) 555-0148</div>

<div class="f-h" style="left:692px;top:4077px">GET IN TOUCH WITH ME FOR INQUIRIES</div>
<div class="field" style="left:692px;top:4128px;width:182px;height:40px">Name</div>
<div class="field" style="left:885px;top:4128px;width:182px;height:40px">Phone</div>
<div class="field" style="left:692px;top:4180px;width:375px;height:41px">Email address</div>
<div class="field" style="left:692px;top:4235px;width:375px;height:115px">Message</div>
<div class="btn submit">SUBMIT NOW</div>

<div class="f-h" style="left:131px;top:4371px">FOLLOW US</div>
<div class="circ social" style="left:289px;background:var(--green)" aria-label="Social profile"></div>
<div class="circ social" style="left:343px;border:1px solid rgba(255,255,255,.25)" aria-label="Social profile"></div>
<div class="circ social" style="left:398px;border:1px solid rgba(255,255,255,.25)" aria-label="Social profile"></div>

<div class="abs copy">© Copyrights 2024 Company name &nbsp;|&nbsp; All Rights Reserved &nbsp;|&nbsp; Terms of service</div>

</body>
</html>
```